Water Management Company Letterhead

Looking for a eye-catching design of letterhead for a California based parent company of water management products. The letterhead would need to include the three logos of the sub-companies, with "The Brookline Collective LLC" (parent company) being the primary focus. Please include the sub-company logos in the following order of significance: Velmoro, Drifting Reeds North, and then Gromtile NE. The color schemes should convey water/enviornment - blues and greens. Most importantly it should be something that will stand out. All logos are uploaded. Thank you for your interest!

Target Market(s)

Environmental conservationists, government agencies, etc.

Industry/Entity Type

Environment

Font styles to use
Serif
Sans Serif

Colors
33a6d7
3276b5
abd037
cadf82
85cae6
85acd3

Requirements
Must have
• eye-catching, blue and green tones pulled from logos, water droplet.

```html
<!DOCTYPE html>
<html lang="en">
<head>
<meta charset="utf-8">
<title>The Brookline Collective LLC — Letterhead</title>
<link rel="stylesheet" href="https://fonts.googleapis.com/css2?family=Cormorant+SC:wght@500&family=Open+Sans:wght@400;700&display=swap">
<style>
  :root {
    --backdrop: #e9eaec;
    --paper: #ffffff;
    --ink: #1f1f24;
    --heading: #2b3346;
    --rule-blue: #3276b5;
    --accent-blue: #33a6d7;
    --accent-green: #abd037;
    --green-soft: #cadf82;
    --drop-grey: #ececec;
  }
  * { box-sizing: border-box; margin: 0; padding: 0; }
  html, body { width: 1200px; height: 1000px; overflow: hidden; }
  body {
    background: var(--backdrop);
    font-family: "Open Sans", Arial, sans-serif;
    color: var(--ink);
    display: flex;
    align-items: center;
    justify-content: center;
  }
  .letterhead {
    position: relative;
    width: 700px;
    height: 930px;
    background: var(--paper);
    box-shadow: 0 6px 24px rgba(0,0,0,0.12);
    padding: 70px 70px 0 70px;
    overflow: hidden;
  }
  .brand {
    display: flex;
    align-items: center;
    gap: 10px;
    margin-left: 40px;
    white-space: nowrap;
  }
  .brand-dot {
    flex: none;
    width: 18px; height: 18px;
    border-radius: 50%;
    background: var(--accent-blue);
  }
  .brand-name {
    font-family: "Cormorant SC", Georgia, serif;
    font-weight: 500;
    font-size: 32px;
    letter-spacing: 1px;
    color: var(--heading);
  }
  .recipient {
    margin-top: 48px;
    font-size: 13px;
    line-height: 1.55;
  }
  .recipient .to { font-weight: 700; }
  .recipient .line { font-weight: 700; padding-left: 14px; }
  .body-copy {
    margin-top: 28px;
    font-size: 12.5px;
    line-height: 1.75;
    max-width: 520px;
    position: relative;
    z-index: 2;
  }
  .body-copy p + p { margin-top: 22px; }
  .sign-off {
    margin-top: 28px;
    font-size: 12.5px;
    position: relative;
    z-index: 2;
  }
  .signature {
    display: block;
    width: 150px;
    height: 50px;
    margin: 8px 0 6px;
  }
  .watermark {
    position: absolute;
    right: -40px;
    bottom: 150px;
    width: 320px;
    height: 420px;
    z-index: 1;
  }
  .footer {
    position: absolute;
    left: 40px; right: 40px;
    bottom: 36px;
  }
  .partners {
    display: flex;
    justify-content: flex-end;
    align-items: center;
    gap: 34px;
    font-size: 13px;
    font-weight: 700;
    color: var(--rule-blue);
    margin-bottom: 12px;
    white-space: nowrap;
  }
  .partner { display: flex; align-items: center; gap: 6px; }
  .partner-mark { width: 10px; height: 10px; border-radius: 50%; background: var(--accent-blue); }
  .partner-mark.square { border-radius: 0; background: var(--accent-green); }
  .rule { height: 2px; background: var(--rule-blue); }
  .contacts {
    display: flex;
    justify-content: flex-end;
    gap: 14px;
    align-items: center;
    margin-top: 10px;
    font-size: 10px;
    color: #333;
    white-space: nowrap;
  }
  .contact { display: flex; align-items: center; gap: 5px; }
  .contact svg { width: 13px; height: 13px; flex: none; }
  .address { border-left: 1px solid #666; padding-left: 12px; }
</style>
</head>
<body>
  <article class="letterhead">
    <header class="brand">
      <span class="brand-dot"></span>
      <span class="brand-name">The Brookline Collective LLC</span>
    </header>

    <section class="recipient">
      <div class="to">To</div>
      <div class="line">Lorem Ipsum is simply</div>
      <div class="line">Lorem Ipsum is Lorem Ipsum is</div>
      <div class="line">Lorem Ipsum is</div>
    </section>

    <section class="body-copy">
      <p>dummy text of the printing and typesetting industry. Lorem Ipsum has been the industry's standard dummy text ever since the 1500s, when an unknown printer took a galley of type and scrambled it to make a type specimen book. It has survived not only five centuries, but also the leap into electronic typesetting, remaining essentially unchanged.</p>
      <p>It is a long established fact that a reader will be distracted by the readable content of a page when looking at its layout. The point of using Lorem Ipsum is that it has a more-or-less normal distribution of letters, as opposed to using 'Content here, content here', making it look like readable English. Many desktop publishing packages and web page editors now use Lorem Ipsum as their default model text, and a search for 'lorem'.</p>
      <p>Contrary to popular belief, Lorem Ipsum is not simply random text. It has roots in a piece of classical Latin literature from 45 BC, making it over 2000 years old. Tomas Ellery, a Latin professor at Harwick-Dale College in Norvale, looked up one of the more obscure Latin words, consectetur, from a Lorem Ipsum passage,</p>
    </section>

    <section class="sign-off">
      <div>Lorem Ipsum</div>
      <svg class="signature" role="img" aria-label="Handwritten signature" viewBox="0 0 150 50">
        <rect width="150" height="50" rx="6" fill="#f1f1f3"/>
      </svg>
      <div>Lorem Ipsum is a dummy</div>
    </section>

    <svg class="watermark" role="img" aria-label="Large faint brand decoration" viewBox="0 0 320 420">
      <defs>
        <radialGradient id="fade" cx="50%" cy="60%" r="60%">
          <stop offset="0%" stop-color="#e6e6e6"/>
          <stop offset="100%" stop-color="#ffffff" stop-opacity="0"/>
        </radialGradient>
      </defs>
      <rect width="320" height="420" fill="url(#fade)"/>
    </svg>

    <footer class="footer">
      <div class="partners">
        <span class="partner"><span class="partner-mark"></span>Velmoro</span>
        <span class="partner"><span class="partner-mark"></span>Drifting Reeds North</span>
        <span class="partner"><span class="partner-mark square"></span>Gromtile NE</span>
      </div>
      <div class="rule"></div>
      <div class="contacts">
        <span class="contact">
          <svg viewBox="0 0 14 14"><rect width="14" height="14" fill="var(--accent-green)"/><path d="M4 3.5c0 3.5 3 6.5 6.5 6.5l.5-1.8-1.8-.8-.9 1c-1.2-.6-2-1.4-2.6-2.6l1-.9-.8-1.8z" fill="#fff"/></svg>
          (000) 300-3000
        </span>
        <span class="contact">
          <svg viewBox="0 0 14 14"><rect width="14" height="14" fill="var(--accent-green)"/><rect x="3" y="4" width="8" height="6" fill="none" stroke="#fff"/><path d="M3 4l4 3 4-3" fill="none" stroke="#fff"/></svg>
          Sales@websitename.com
        </span>
        <span class="contact">
          <svg viewBox="0 0 14 14"><rect width="14" height="14" fill="var(--accent-green)"/><circle cx="7" cy="7" r="3.5" fill="none" stroke="#fff"/><path d="M3.5 7h7M7 3.5v7" stroke="#fff"/></svg>
          www.websitename.com
        </span>
        <span class="contact address">0000 E. Address Line, Fernhollow, CA 0000</span>
      </div>
    </footer>
  </article>
</body>
</html>
```